Defense Attorney Business Card Design Project/ Stationary

I am looking for a distinctive business card design for my solo law practice.
I practice criminal defense, both juvenile and adult, including DUI. I am a very experienced attorney with prior military experience. The design should convey a traditional, old school flair, but not be too stodgy or uptight. Some color. My logo should appear.
Updates

Project Deadline Extended Reason: I misunderstood how this project works and I was not prepared with my logo when this project ran the first time. Added Thursday, November 13, 2014

Project Deadline Extended
Reason: I was sent overseas on military duty last year, which interrupted this project. Thank you for your participation... I hope we can get this done this week! Thank you, Neil

Target Market(s)

Regular everyday people looking for strong, knowledgeable, authoritative representation while they are faced with criminal charges. Many have never been charged with a crime before. A reassuring air is therefore desired.

Industry/Entity Type

Business

Contact Information for Business Card

My information is:
Theodore M. Quill, Attorney at Law
785 Birch Avenue Suite 300
Oakland, California 94719
Tel: (510) 384-6125
Fax: (510) 391-7802
email: neilquilllaw@mailvine.example
web: www.neilquilllaw.example

Font styles to use
Serif
Sans Serif
Decorative

Colors
0255a3
ffffff

Requirements
Must have
• Sharp lines, bold elements. Conservative use of colors, such as deep blues, burgundy, grays for example.
• While my logo says "Theodore M. Quill", it should be modified to show "Theodore M. Quill".
Should not have
• Cliche imagery such as scales of justice, gavels, Statue of Liberty, etc.

```html
<!DOCTYPE html>
<html lang="en">
<head>
<meta charset="utf-8">
<title>Theodore M. Quill Law – Business Card</title>
<link href="https://fonts.googleapis.com/css2?family=Open+Sans:wght@400;600&display=swap" rel="stylesheet">
<style>
  :root {
    --stage: #e4e5e7;
    --paper: #ffffff;
    --navy: #17394f;
    --navy-deep: #0e2737;
    --navy-light: #24506b;
    --silver: #c9ced3;
    --silver-dark: #8d959c;
    --text-light: #e9eef2;
    --text-muted: #b9c6cf;
  }
  * { box-sizing: border-box; margin: 0; padding: 0; }
  html, body { width: 1200px; height: 900px; overflow: hidden; }
  body {
    background: var(--stage);
    display: flex;
    align-items: center;
    justify-content: center;
    gap: 44px;
    font-family: "Open Sans", Arial, sans-serif;
  }
  .card {
    position: relative;
    width: 530px;
    height: 306px;
    border-radius: 22px;
    overflow: hidden;
  }

  /* Wordmark */
  .brand-name {
    font-family: "Open Sans", Arial, sans-serif;
    font-weight: 600;
    font-size: 26px;
    color: var(--navy);
    line-height: 1;
    padding-bottom: 6px;
    border-bottom: 1.5px solid var(--navy);
  }
  .brand-tagline {
    font-family: "Open Sans", Arial, sans-serif;
    font-weight: 600;
    font-size: 10px;
    letter-spacing: 1px;
    color: var(--navy);
    margin-top: 6px;
  }

  /* Front */
  .card--front { background: var(--paper); }
  .front__brand {
    height: 150px;
    display: flex;
    flex-direction: column;
    align-items: center;
    justify-content: flex-end;
    padding-bottom: 14px;
  }
  .front__rule {
    height: 8px;
    background: linear-gradient(90deg, var(--silver-dark), #eef0f2 45%, var(--silver) 70%, var(--silver-dark));
  }
  .front__details {
    position: absolute;
    left: 0; right: 0; bottom: 0;
    top: 158px;
    background: linear-gradient(100deg, var(--navy-light), var(--navy) 50%, var(--navy-deep));
    display: flex;
    padding-top: 20px;
  }
  .person {
    width: 205px;
    text-align: right;
    padding-right: 18px;
    border-right: 1px solid var(--text-muted);
    height: 108px;
  }
  .person__name { font-size: 16px; color: var(--text-light); }
  .person__title { font-size: 13px; color: var(--text-light); margin-top: 2px; }
  .contact { list-style: none; padding-left: 16px; color: var(--text-light); font-size: 13px; line-height: 17px; }
  .contact li { display: flex; align-items: flex-start; gap: 6px; }
  .contact li + li.group { margin-top: 6px; }
  .contact svg { width: 12px; height: 12px; margin-top: 2px; flex: none; fill: var(--text-light); }

  /* Back */
  .card--back {
    background: radial-gradient(ellipse at 58% 50%, var(--navy-light) 0%, var(--navy) 45%, var(--navy-deep) 100%);
    display: flex;
    flex-direction: column;
    align-items: center;
    justify-content: center;
    padding-top: 40px;
  }
  .card--back .brand-name { color: var(--silver); border-color: var(--silver); font-size: 28px; }
  .card--back .brand-tagline { color: var(--silver); }
</style>
</head>
<body>
  <section class="card card--front" aria-label="Business card front">
    <header class="front__brand">
      <div class="brand-name">Theodore M. Quill Law</div>
      <div class="brand-tagline">DUI - CRIMINAL DEFENSE - 420</div>
    </header>
    <div class="front__rule"></div>
    <div class="front__details">
      <div class="person">
        <p class="person__name">Theodore M. Quill</p>
        <p class="person__title">Attorney</p>
      </div>
      <ul class="contact">
        <li>
          <svg viewBox="0 0 12 12"><path d="M6 1 0.5 6H2v5h3V8h2v3h3V6h1.5z"/></svg>
          <span>785 Birch Avenue Suite 300<br>Oakland, California 94719</span>
        </li>
        <li class="group">
          <svg viewBox="0 0 12 12"><path d="M2.5 1 4.5 1 5.2 3.8 4 4.8C4.7 6.3 5.7 7.3 7.2 8L8.2 6.8 11 7.5V9.5C11 10.3 10.3 11 9.5 11 5 11 1 7 1 2.5 1 1.7 1.7 1 2.5 1z"/></svg>
          <span>(510) 384-6125</span>
        </li>
        <li>
          <svg viewBox="0 0 12 12"><path d="M3 1h5v3H3zM1 5h10v5H1zM3 8h6v3H3z"/></svg>
          <span>(510) 391-7802</span>
        </li>
        <li class="group">
          <svg viewBox="0 0 12 12"><path d="M1 3h10v7H1zM1.8 3.6 6 7l4.2-3.4" stroke="#17394f" stroke-width="0.9"/></svg>
          <span>neilquilllaw@mailvine.example</span>
        </li>
        <li>
          <svg viewBox="0 0 12 12"><circle cx="6" cy="6" r="5"/><path d="M1 6h10M6 1c-2.5 2.5-2.5 7.5 0 10M6 1c2.5 2.5 2.5 7.5 0 10" stroke="#17394f" stroke-width="0.8" fill="none"/></svg>
          <span>www.neilquilllaw.example</span>
        </li>
      </ul>
    </div>
  </section>

  <section class="card card--back" aria-label="Business card back">
    <div class="brand-name">Theodore M. Quill Law</div>
    <div class="brand-tagline">DUI - CRIMINAL DEFENSE - 420</div>
  </section>
</body>
</html>
```